Business Cards for company that supports physicians that do medical research

Need to create a business card for Qorvel Studies (www.qorvelstudies.example), a company devoted to supporting physicians who conduct medical research. The form of the card should match the message of research and information quest. I have provided the logo of the company as an uploaded file. Designs should be simple and slick aimed at very high end clients.

Target Market(s)

Medical doctors that are also researchers

Industry/Entity Type

Medical

Contact Information for Business Card

Should feature logo and fields for personal info:
Name/title
Phone /email

Font styles to use
Serif
Sans Serif

Requirements
Must have
• Qorvel logo and fields for personal info:
• Name: Bertrand Okonfu
• Title: VP Research and Senior Analyst
• Phone: 555-203-4719
• email: info@qorvelstudies.example
Nice to have
• Interesting cards that I've seen:
• 1- all black/charcoal or very dark background
• 2- Plastic - semi-transparent
• 3- non-standard height-width ratios
• 4- Functional cards -- USB drive incorporated
Should not have
• Too busy; needs to stay very simple

```html
<!DOCTYPE html>
<html lang="en">
<head>
<meta charset="utf-8">
<title>Qorvel Studies – Business Card</title>
<link rel="stylesheet" href="https://fonts.googleapis.com/css2?family=Open+Sans:wght@400;600&display=swap">
<style>
  :root {
    --page-bg: #e9e7e4;
    --card-bg: #2a2928;
    --card-bg-deep: #201f1e;
    --accent-green: #5cc84a;
    --accent-blue: #1f8fd0;
    --text-light: #f4f4f4;
  }
  * { margin: 0; padding: 0; box-sizing: border-box; }
  html, body {
    width: 1200px;
    height: 900px;
    overflow: hidden;
    background: var(--page-bg);
    font-family: "Open Sans", sans-serif;
  }
  .canvas {
    position: relative;
    width: 1200px;
    height: 900px;
  }
  .business-card {
    position: absolute;
    left: 160px;
    top: 180px;
    width: 880px;
    height: 540px;
    background: linear-gradient(160deg, var(--card-bg) 0%, var(--card-bg-deep) 100%);
    border-radius: 0 84px 0 84px;
    box-shadow: 0 18px 40px rgba(0, 0, 0, 0.22);
  }
  .holder {
    position: absolute;
    right: 52px;
    top: 72px;
    text-align: right;
  }
  .holder-name {
    color: var(--accent-green);
    font-weight: 600;
    font-size: 29px;
    line-height: 1.2;
  }
  .holder-title {
    color: var(--text-light);
    font-weight: 400;
    font-size: 21px;
    margin-top: 6px;
  }
  .brand {
    position: absolute;
    left: 52px;
    top: 190px;
    display: flex;
    align-items: center;
    gap: 18px;
  }
  .brand-dot {
    width: 26px;
    height: 26px;
    border-radius: 50%;
    background: var(--accent-blue);
  }
  .brand-name {
    color: var(--accent-green);
    font-weight: 600;
    font-size: 62px;
    line-height: 1;
    letter-spacing: -0.5px;
  }
  .contact-list {
    position: absolute;
    right: 52px;
    top: 420px;
    list-style: none;
  }
  .contact-item {
    display: flex;
    align-items: center;
    justify-content: flex-end;
    gap: 12px;
    color: var(--text-light);
    font-size: 21px;
    height: 36px;
  }
  .contact-icon {
    width: 26px;
    height: 26px;
    border-radius: 4px;
    background: var(--accent-green);
    display: flex;
    align-items: center;
    justify-content: center;
  }
</style>
</head>
<body>
<main class="canvas">
  <section class="business-card">
    <div class="holder">
      <p class="holder-name">Bertrand Okonfu</p>
      <p class="holder-title">VP Research and Senior Analyst</p>
    </div>

    <div class="brand">
      <span class="brand-dot"></span>
      <span class="brand-name">Qorvel Studies</span>
    </div>

    <ul class="contact-list">
      <li class="contact-item">
        <span>555-203-4719</span>
        <span class="contact-icon">
          <svg width="16" height="16" viewBox="0 0 16 16" aria-hidden="true">
            <path d="M3 3.5c1.2-1 2.2-.8 2.7.2l.8 1.6c.3.6.1 1.2-.4 1.6l-.7.5c.6 1.3 1.6 2.3 2.9 2.9l.5-.7c.4-.5 1-.7 1.6-.4l1.6.8c1 .5 1.2 1.5.2 2.7-1 1.2-2.7 1.3-4.6.1C5.8 11.6 4.4 10.2 3.2 8.3 2 6.4 2 4.6 3 3.5z" fill="#fff"/>
          </svg>
        </span>
      </li>
      <li class="contact-item">
        <span>info@qorvelstudies.example</span>
        <span class="contact-icon">
          <svg width="16" height="16" viewBox="0 0 16 16" aria-hidden="true">
            <rect x="2" y="4" width="12" height="8.5" rx="1" fill="#fff"/>
            <path d="M2.5 4.6 8 9l5.5-4.4" fill="none" stroke="#5cc84a" stroke-width="1.2"/>
          </svg>
        </span>
      </li>
    </ul>
  </section>
</main>
</body>
</html>
```